MV Decor

There is a sample provided with the arabic text of the business card. please copy paste the same text and the same Logo (The two triangles) Just try to incorproate the Brown background attached (you are free to change the colors) Id like the colors to be mainly shades of black and red.

```html
<!DOCTYPE html>
<html lang="ar">
<head>
<meta charset="utf-8">
<title>MV Decor – Business Card</title>
<link rel="stylesheet" href="https://fonts.googleapis.com/css2?family=Aref+Ruqaa:wght@400;700&family=Tajawal:wght@400;500&family=Roboto:wght@400;700&display=swap">
<style>
  :root {
    --page: #ece9e5;
    --red: #c91f42;
    --red-light: #d83a57;
    --red-deep: #b3183a;
    --ink: #262624;
    --white: #ffffff;
  }
  * { margin: 0; padding: 0; box-sizing: border-box; }
  html, body { width: 1125px; height: 1200px; overflow: hidden; background: var(--page); }
  .canvas { position: relative; width: 1125px; height: 1200px; }

  .card {
    position: absolute;
    left: 171px;
    width: 826px;
    height: 472px;
    overflow: hidden;
    box-shadow: 0 3px 8px rgba(0,0,0,.25);
  }
  .card--front { top: 106px; }
  .card--back { top: 639px; }

  .card__texture {
    position: absolute; inset: 0;
    background:
      radial-gradient(ellipse at 35% 30%, var(--red-light) 0%, transparent 55%),
      radial-gradient(ellipse at 75% 75%, var(--red-light) 0%, transparent 50%),
      linear-gradient(160deg, var(--red) 0%, var(--red-deep) 100%);
  }

  .contact-bar {
    position: absolute; left: 0; right: 0; bottom: 0;
    height: 45px;
    background: var(--ink);
    display: flex; align-items: center;
    padding-left: 57px;
    font-family: "Roboto", sans-serif;
    font-size: 21px;
    color: var(--white);
  }
  .contact-bar svg { width: 19px; height: 19px; margin-right: 9px; fill: var(--white); }

  .profile {
    position: absolute;
    right: 532px;
    top: 198px;
    direction: rtl;
    text-align: right;
    color: var(--white);
  }
  .profile__name {
    font-family: "Aref Ruqaa", serif;
    font-size: 25px;
    line-height: 1.1;
    white-space: nowrap;
  }
  .profile__title {
    font-family: "Aref Ruqaa", serif;
    font-size: 17px;
    margin: 6px 65px 14px 0;
  }
  .profile__quals {
    list-style: none;
    font-family: "Tajawal", sans-serif;
    font-size: 21px;
    line-height: 28px;
    white-space: nowrap;
  }

  .brand-name {
    position: absolute;
    font-family: "Roboto", sans-serif;
    font-weight: 700;
    color: var(--white);
    letter-spacing: 1px;
    white-space: nowrap;
  }
  .card--front .brand-name { left: 558px; top: 232px; font-size: 44px; }
  .card--back .brand-name { left: 127px; top: 210px; font-size: 52px; }

  .services {
    position: absolute;
    right: 141px;
    top: 82px;
    list-style: none;
    direction: rtl;
    font-family: "Tajawal", sans-serif;
    font-size: 25px;
    line-height: 33px;
    color: var(--white);
    white-space: nowrap;
  }
  .services li::after {
    content: "";
    display: inline-block;
    width: 8px; height: 8px;
    margin-right: 10px;
    border-radius: 50%;
    background: var(--white);
    vertical-align: middle;
  }
</style>
</head>
<body>
<main class="canvas">

  <section class="card card--front" aria-label="Card front">
    <div class="card__texture" role="img" aria-label="Red mosaic pattern background"></div>

    <div class="profile">
      <p class="profile__name">المهندس / سالم يوسف الراشد</p>
      <p class="profile__title">أستاذ جامعي</p>
      <ul class="profile__quals">
        <li>ماجستير هندسة ديكور</li>
        <li>دبلوم عالي فن تشكيلي</li>
        <li>جامعة الفنون (باريس)</li>
        <li>استشارات هندسية - فنية</li>
      </ul>
    </div>

    <p class="brand-name">MV DECOR</p>

    <div class="contact-bar">
      <svg viewBox="0 0 24 24" aria-hidden="true"><path d="M6.6 10.8a15.1 15.1 0 0 0 6.6 6.6l2.2-2.2c.3-.3.7-.4 1-.2 1.1.4 2.3.6 3.6.6.6 0 1 .4 1 1V20c0 .6-.4 1-1 1A17 17 0 0 1 3 4c0-.6.4-1 1-1h3.5c.6 0 1 .4 1 1 0 1.3.2 2.5.6 3.6.1.3 0 .7-.2 1z"/></svg>
      <span>39450216 / 66120948</span>
    </div>
  </section>

  <section class="card card--back" aria-label="Card back">
    <div class="card__texture" role="img" aria-label="Red mosaic pattern background"></div>

    <p class="brand-name">MV DECOR</p>

    <ul class="services">
      <li>ماجستير هندسة ديكور</li>
      <li>دبلوم عالي فن تشكيلي</li>
      <li>جامعة الفنون (باريس)</li>
      <li>استشارات هندسية - فنية</li>
      <li>ماجستير هندسة ديكور</li>
      <li>دبلوم عالي فن تشكيلي</li>
      <li>جامعة الفنون (باريس)</li>
      <li>استشارات هندسية - فنية</li>
    </ul>
  </section>

</main>
</body>
</html>
```